We are a recruitment company based in Norwich/Cambridge England.
I have included our company logo which we want to remain the same.

What we are looking for is a new creative Business card which will really stand out!!

Contact Information for Business Card

Harriet Dunmore
email: Harriet@plavex.co.uk
Address: Brackwell House
Fenmoor Enterprise Park
Partridge Way
Norwich
QB9 3KX
Tel:01632 960418

```html
<!DOCTYPE html>
<html lang="en">
<head>
<meta charset="utf-8">
<title>Plavex Business Card</title>
<link rel="stylesheet" href="https://fonts.googleapis.com/css2?family=Poppins:wght@400;600&family=Arimo:wght@400;700&display=swap">
<style>
  :root {
    --backdrop: #1d1d20;
    --card: #050505;
    --green: #7cc242;
    --grey: #8d8b91;
    --text-light: #d9d9d9;
  }
  * { margin: 0; padding: 0; box-sizing: border-box; }
  html, body { width: 1200px; height: 800px; overflow: hidden; }
  body {
    background: var(--backdrop);
    position: relative;
    font-family: "Arimo", Arial, sans-serif;
  }
  .card {
    position: absolute;
    top: 250px;
    width: 520px;
    height: 300px;
    background: var(--card);
    overflow: hidden;
    box-shadow: 0 14px 30px rgba(0,0,0,0.55);
  }
  .card--front { left: 50px; }
  .card--back { left: 630px; }

  .edge-band {
    position: absolute;
    left: 0; right: 0; bottom: 0;
    height: 10px;
    display: flex;
  }
  .edge-band__grey { flex: 0 0 55%; background: var(--grey); }
  .edge-band__green { flex: 1; background: var(--green); }

  .brand {
    position: absolute;
    display: flex;
    align-items: center;
    gap: 14px;
  }
  .card--front .brand { left: 50%; top: 48%; transform: translate(-50%, -50%); }
  .card--back .brand { left: 40px; top: 160px; transform: scale(0.8); transform-origin: left center; }
  .brand__dot {
    width: 62px; height: 62px;
    border-radius: 50%;
    background: var(--green);
  }
  .brand__words { display: flex; flex-direction: column; }
  .brand__name {
    font-family: "Poppins", Arial, sans-serif;
    font-weight: 600;
    font-size: 54px;
    line-height: 1;
    color: var(--green);
    letter-spacing: -1px;
  }
  .brand__tagline {
    font-family: "Poppins", Arial, sans-serif;
    font-size: 9px;
    letter-spacing: 3px;
    color: var(--grey);
    margin-top: 4px;
    text-align: right;
  }

  .divider {
    position: absolute;
    left: 268px;
    top: 55px;
    width: 1px;
    height: 175px;
    background: linear-gradient(var(--green), #2d4a18);
  }

  .contact {
    position: absolute;
    left: 288px;
    top: 48px;
    width: 220px;
    color: var(--text-light);
    font-size: 12px;
    line-height: 1.35;
  }
  .contact__name {
    color: var(--green);
    font-weight: 700;
    font-size: 19px;
    line-height: 1.1;
  }
  .contact__role { font-size: 12px; margin-bottom: 12px; }
  .contact__row { display: flex; align-items: center; gap: 7px; margin-bottom: 2px; white-space: nowrap; }
  .contact__icon { width: 14px; height: 14px; flex: 0 0 14px; }
  .contact__address { margin-top: 10px; padding-left: 21px; }
</style>
</head>
<body>

<section class="card card--front" aria-label="Business card front">
  <div class="brand">
    <span class="brand__dot"></span>
    <div class="brand__words">
      <span class="brand__name">Plavex</span>
      <span class="brand__tagline">Technology Recruitment</span>
    </div>
  </div>
  <div class="edge-band"><span class="edge-band__grey"></span><span class="edge-band__green"></span></div>
</section>

<section class="card card--back" aria-label="Business card back">
  <div class="brand">
    <span class="brand__dot"></span>
    <div class="brand__words">
      <span class="brand__name">Plavex</span>
      <span class="brand__tagline">Technology Recruitment</span>
    </div>
  </div>

  <span class="divider"></span>

  <div class="contact">
    <p class="contact__name">Harriet Dunmore</p>
    <p class="contact__role">CEO</p>
    <p class="contact__row">
      <svg class="contact__icon" viewBox="0 0 14 14" aria-hidden="true">
        <circle cx="7" cy="7" r="6.2" fill="none" stroke="#7cc242" stroke-width="1.2"/>
        <rect x="5" y="3.5" width="4" height="7" rx="0.8" fill="none" stroke="#7cc242" stroke-width="1"/>
      </svg>01632 960418</p>
    <p class="contact__row">
      <svg class="contact__icon" viewBox="0 0 14 14" aria-hidden="true">
        <circle cx="7" cy="7" r="6.2" fill="none" stroke="#7cc242" stroke-width="1.2"/>
        <rect x="3.8" y="4.8" width="6.4" height="4.4" fill="none" stroke="#7cc242" stroke-width="1"/>
        <path d="M3.8 4.8 L7 7.4 L10.2 4.8" fill="none" stroke="#7cc242" stroke-width="1"/>
      </svg>Harriet@plavex.co.uk</p>
    <p class="contact__row">
      <svg class="contact__icon" viewBox="0 0 14 14" aria-hidden="true">
        <circle cx="7" cy="7" r="6.2" fill="none" stroke="#7cc242" stroke-width="1.2"/>
        <circle cx="7" cy="7" r="3.4" fill="none" stroke="#7cc242" stroke-width="0.9"/>
        <path d="M3.6 7 H10.4 M7 3.6 V10.4" stroke="#7cc242" stroke-width="0.9"/>
      </svg>www.plavex.co.uk</p>
    <p class="contact__address">Brackwell House<br>Fenmoor Enterprise Park<br>Partridge Way<br>Norwich QB9 3KX</p>
  </div>

  <div class="edge-band"><span class="edge-band__grey"></span><span class="edge-band__green"></span></div>
</section>

</body>
</html>
```